The Linen Loft Co

We need a business card design for our wardrobe company.
Please visit our website www.gentlelinenlofts.com to get an idea of who we are.

```html
<!DOCTYPE html>
<html lang="en">
<head>
<meta charset="utf-8">
<title>The Linen Loft Co — Business Card</title>
<link rel="stylesheet" href="https://fonts.googleapis.com/css2?family=Montserrat:wght@500;600;700&family=Open+Sans:wght@400;600&display=swap">
<style>
  :root {
    --backdrop: #2a2a2b;
    --card: #1a1a1a;
    --gold: #a88d5e;
    --white: #ffffff;
    --icon-ink: #1a1a1a;
  }
  * { margin: 0; padding: 0; box-sizing: border-box; }
  html, body {
    width: 1200px; height: 900px; overflow: hidden;
    background: var(--backdrop);
  }
  .canvas { position: relative; width: 1200px; height: 900px; }
  .card {
    position: absolute; left: 270px;
    width: 660px; height: 390px;
    background: var(--card);
    border-radius: 26px;
    box-shadow: 0 18px 40px rgba(0,0,0,.45);
  }
  .card--front { top: 40px; }
  .card--back { top: 470px; }

  .brand {
    position: absolute; left: 70px;
    display: flex; align-items: center; gap: 26px;
  }
  .card--front .brand { top: 118px; }
  .card--back .brand { top: 40px; }
  .brand__mark {
    width: 90px; height: 90px;
    border: 3px solid var(--gold);
    flex: none;
  }
  .brand__text { color: var(--gold); font-family: "Montserrat", sans-serif; }
  .brand__name {
    font-weight: 600; font-size: 27px; letter-spacing: 2.5px;
    text-transform: uppercase; line-height: 1.1;
  }
  .brand__tagline {
    font-weight: 600; font-size: 24px; letter-spacing: 1px;
    margin-top: 8px; margin-left: 18px;
  }

  .divider {
    position: absolute; left: 28px; right: 28px; top: 185px;
    height: 1.5px; background: var(--gold);
  }
  .person { position: absolute; left: 0; right: 0; top: 200px; text-align: center; }
  .person__name {
    font-family: "Montserrat", sans-serif; font-weight: 700;
    font-size: 26px; color: var(--gold);
  }
  .person__role {
    font-family: "Open Sans", sans-serif; font-weight: 600;
    font-size: 19px; color: var(--white); margin-top: 2px;
  }
  .contact-icons {
    position: absolute; left: 0; right: 0; top: 278px;
    display: flex; justify-content: center; gap: 12px;
  }
  .contact-icons svg { width: 30px; height: 30px; }
  .contact-list {
    position: absolute; left: 0; right: 0; top: 316px;
    text-align: center; list-style: none;
    font-family: "Open Sans", sans-serif; font-size: 17px;
    color: var(--white); line-height: 1.3; letter-spacing: .5px;
  }
  .contact-list .accent { color: var(--gold); }
</style>
</head>
<body>
<main class="canvas">
  <section class="card card--front">
    <div class="brand">
      <div class="brand__mark"></div>
      <div class="brand__text">
        <p class="brand__name">The Linen Loft Co</p>
        <p class="brand__tagline">Folded with Quiet Care</p>
      </div>
    </div>
  </section>

  <section class="card card--back">
    <div class="brand">
      <div class="brand__mark"></div>
      <div class="brand__text">
        <p class="brand__name">The Linen Loft Co</p>
        <p class="brand__tagline">Folded with Quiet Care</p>
      </div>
    </div>
    <div class="divider"></div>
    <div class="person">
      <p class="person__name">Dana Whitlow</p>
      <p class="person__role">Manager</p>
    </div>
    <div class="contact-icons">
      <svg viewBox="0 0 30 30" aria-label="Phone">
        <circle cx="15" cy="15" r="14" fill="var(--gold)" stroke="var(--white)" stroke-width="1"/>
        <path d="M11 9 l3 0 l1 4 l-2 1 a7 7 0 0 0 3 3 l1 -2 l4 1 l0 3 a2 2 0 0 1 -2 1 a11 11 0 0 1 -9 -9 a2 2 0 0 1 1 -2z" fill="var(--icon-ink)"/>
      </svg>
      <svg viewBox="0 0 30 30" aria-label="Email">
        <circle cx="15" cy="15" r="14" fill="var(--gold)" stroke="var(--white)" stroke-width="1"/>
        <rect x="9" y="11" width="12" height="8" fill="none" stroke="var(--icon-ink)" stroke-width="1.6"/>
        <path d="M9 11 l6 5 l6 -5" fill="none" stroke="var(--icon-ink)" stroke-width="1.6"/>
      </svg>
      <svg viewBox="0 0 30 30" aria-label="Website">
        <circle cx="15" cy="15" r="14" fill="var(--gold)" stroke="var(--white)" stroke-width="1"/>
        <circle cx="15" cy="15" r="6" fill="none" stroke="var(--icon-ink)" stroke-width="1.6"/>
        <path d="M9 15 h12 M15 9 c-3 3 -3 9 0 12 M15 9 c3 3 3 9 0 12" fill="none" stroke="var(--icon-ink)" stroke-width="1.2"/>
      </svg>
    </div>
    <ul class="contact-list">
      <li>555-014-2290</li>
      <li>info@gentlelinenlofts.com</li>
      <li>www.<span class="accent">gentlelinenlofts</span>.com</li>
    </ul>
  </section>
</main>
</body>
</html>
```